Private Investment Firm Needs PowerPoint Presentation Template

Design PowerPoint template, take Pinebrook-submitted rough presentation draft, and drop it into new template. See attached Project Brief file for more detail.
Updates

Some decent designs have been submitted but they seem to lack the understanding of our target markets. I am hopeful that more time and feedback will result in better results.

Target Market(s)

Private company owners and intermediaries.

Font styles to use
Serif

Colors
3176b5

Requirements
Must have
• See attached Project Brief.
Nice to have
Should not have
• No B2C fluff--this is a B2B project.

```html
<!DOCTYPE html>
<html lang="en">
<head>
<meta charset="utf-8">
<title>What Is Non-Control Capital? – Pinebrook Capital</title>
<link rel="stylesheet" href="https://fonts.googleapis.com/css2?family=Montserrat:wght@600;700&family=Figtree:wght@400;500&family=Libre+Baskerville&display=swap">
<style>
  :root {
    --brand-blue: #0b6bbd;
    --rail-blue: #0a6ac0;
    --ink: #1f1f1f;
    --paper: #ffffff;
    --photo-light: #c9d6e4;
    --photo-mid: #5f7fa8;
    --photo-dark: #1d2f4e;
  }
  * { margin: 0; padding: 0; box-sizing: border-box; }
  html, body { width: 1200px; height: 676px; overflow: hidden; background: var(--paper); }
  .slide { position: relative; width: 1200px; height: 676px; background: var(--paper); font-family: "Figtree", sans-serif; color: var(--ink); }

  .side-rail { position: absolute; left: 0; top: 0; width: 44px; height: 676px; background: var(--rail-blue); }
  .side-rail__url {
    position: absolute; left: 22px; top: 337px;
    transform: translate(-50%, -50%) rotate(-90deg);
    white-space: nowrap; color: var(--paper);
    font-family: "Libre Baskerville", serif; font-size: 14px; letter-spacing: 0.2px;
  }

  .slide-title {
    position: absolute; left: 88px; top: 80px;
    font-family: "Montserrat", sans-serif; font-weight: 700; font-size: 29px;
    color: var(--brand-blue); letter-spacing: 0.3px;
  }

  .point { position: absolute; left: 88px; width: 630px; font-size: 17.2px; line-height: 28px; letter-spacing: 0.3px; padding-left: 26px; }
  .point__marker { position: absolute; left: 0; top: 7px; width: 14px; height: 14px; }
  .point--intro { top: 144px; padding-left: 28px; }
  .point--alignment { top: 410px; }
  .point--essence { top: 466px; }

  .retained-controls { position: absolute; left: 88px; top: 253px; display: grid; grid-template-columns: 310px 310px; grid-auto-rows: 58px; column-gap: 10px; row-gap: 14px; }
  .retained-controls__item {
    background: var(--brand-blue); color: var(--paper);
    display: flex; align-items: center; padding-left: 36px;
    font-size: 14.4px; line-height: 18px; letter-spacing: 0.2px;
  }

  .brand-mark { position: absolute; left: 68px; top: 616px; display: flex; align-items: center; gap: 10px; }
  .brand-mark__dot { width: 34px; height: 34px; border-radius: 50%; background: var(--brand-blue); }
  .brand-mark__name { font-family: "Montserrat", sans-serif; font-weight: 600; font-size: 20px; color: var(--brand-blue); letter-spacing: 1px; }

  .hero-photo {
    position: absolute; left: 760px; top: 0; width: 428px; height: 676px;
    background: linear-gradient(160deg, var(--photo-light) 0%, var(--photo-mid) 35%, var(--photo-dark) 60%, #c7d3e2 85%, #e8eef5 100%);
  }
  .edge-rail { position: absolute; left: 1188px; top: 0; width: 12px; height: 676px; background: var(--rail-blue); }
  .page-number { position: absolute; left: 1156px; top: 18px; font-family: "Libre Baskerville", serif; font-size: 15px; color: #2a2a2a; }
</style>
</head>
<body>
<main class="slide">
  <aside class="side-rail"><span class="side-rail__url">www.pinebrookcapital.com</span></aside>

  <h1 class="slide-title">WHAT IS NON-CONTROL CAPITAL?</h1>

  <p class="point point--intro">
    <svg class="point__marker" viewBox="0 0 14 14" aria-hidden="true"><rect x="3" y="3" width="8" height="8" transform="rotate(45 7 7)" fill="none" stroke="#0b6bbd" stroke-width="3"/></svg>
    Non-Control Capital is an investment which is primarily used for the ongoing operation and/or growth of a business but also allows the current owners to retain:
  </p>

  <div class="retained-controls">
    <div class="retained-controls__item">Control of the Business Economics</div>
    <div class="retained-controls__item">Control of the Business Operations</div>
    <div class="retained-controls__item">Control of Strategy and Key<br>Decision Making</div>
    <div class="retained-controls__item">Control of the Board of Directors</div>
  </div>

  <p class="point point--alignment">
    <svg class="point__marker" viewBox="0 0 14 14" aria-hidden="true"><rect x="3" y="3" width="8" height="8" transform="rotate(45 7 7)" fill="none" stroke="#0b6bbd" stroke-width="3"/></svg>
    Requires the alignment of management incentives with ownership
  </p>

  <p class="point point--essence">
    <svg class="point__marker" viewBox="0 0 14 14" aria-hidden="true"><rect x="3" y="3" width="8" height="8" transform="rotate(45 7 7)" fill="none" stroke="#0b6bbd" stroke-width="3"/></svg>
    In essence, a company receives the capital it needs to implement its business plans but owners continue to retain ultimate control
  </p>

  <div class="brand-mark">
    <span class="brand-mark__dot"></span>
    <span class="brand-mark__name">PINEBROOK CAPITAL</span>
  </div>

  <div class="hero-photo" role="img" aria-label="Photo of a businessman reviewing blue bar and pie charts on a laptop screen, with a pen and printed charts on the desk"></div>
  <div class="edge-rail"></div>
  <span class="page-number">2</span>
</main>
</body>
</html>
```